Blow Dry Bar Business Cards

These cards must be eye catching and modern.
You must be willing to work fast and make changes.

Winner will be offered other projects

Files 1 THIS IS THE STYLE CARDS I AM INTRESTED IN!!!
Please be creative, I am paying for my own eye catching design. I need files to be nexa press ready.

COLORS THAT ARE PAINTED INSIDE MY SHOP:
- - - http://www.quorvelpaint.example/en/explore-colors/painter/color-selector.html?colors=4007-3C

- - - http://www.brandivex.example/color/paint-colors/hidden-corridor-d58-2

I want the business cards sleek and modern if you use the logo please correct imperfections. I added the part that says Blow Dry Bar (see website).
Do not be afraid to separate the blow dryer from the name to make the cards look like the file with the pink elephant.

SHOULD INCLUDE
*Blow Dryer (we are a blow dry bar not a salon we do not cut or color so do not include sheers of any kind)
*BUSINESS NAME: Simply Swept Upward - Blow Dry Bar (PLEASE SEE MY WEBSITE)
* Website: SIMPLYSWEPTUPWARD.EXAMPLE
*Phone number (555) 014-2763
Updates

Nexa press said it can be submitted in JPG

http://www.brandivex.example/color/paint-colors/hidden-corridor-d58-2 http://www.quorvelpaint.example/en/explore-colors/painter/color-selector.html?colors=4007-3C ^^^^ These links will take you to the color paint that is painted inside my shop.

Target Market(s)

AGES 18 - 55 WOMEN
HIGH END MARKET

Industry/Entity Type

Salon

Requirements
Must have
• SEE COLOR EXAMPLE FILE
BLOW DRYER
UNIQUE
I LIKE THE CARD WITH THE PINK ELEPHANT THE BEST
Nice to have
• BE AS CREATIVE AND MODERN AS POSSIBLE DO NOT COPY ANY OF THE CARDS BELOW.
Should not have
• SCISSORS
PINK

```html
<!DOCTYPE html>
<html lang="en">
<head>
<meta charset="utf-8">
<title>Blow Dry Bar Business Cards</title>
<link href="https://fonts.googleapis.com/css2?family=Josefin+Sans:wght@300;400&family=Alike&display=swap" rel="stylesheet">
<style>
  :root {
    --backdrop: #e9e6e1;
    --card-dark: #2b2b2b;
    --card-mid: #3a3a3a;
    --ink-light: #f2f2f2;
    --band-light: #dcdcdc;
    --band-ink: #3a3a3a;
    --rule: #d8d8d8;
  }
  html, body {
    margin: 0;
    padding: 0;
    width: 1200px;
    height: 885px;
    overflow: hidden;
    background: var(--backdrop);
  }
  .canvas {
    width: 1200px;
    height: 885px;
    display: flex;
    align-items: center;
    justify-content: center;
    gap: 44px;
  }
  .card {
    position: relative;
    width: 540px;
    height: 315px;
    border-radius: 16px;
    overflow: hidden;
    background: radial-gradient(ellipse at 50% 40%, var(--card-mid), var(--card-dark) 75%);
    box-shadow: 0 10px 24px rgba(0,0,0,0.25);
    color: var(--ink-light);
    font-family: "Josefin Sans", sans-serif;
    font-weight: 300;
  }
  /* Front */
  .front .title {
    position: absolute;
    top: 54px;
    left: 0;
    right: 0;
    text-align: center;
    font-size: 50px;
    letter-spacing: 1px;
  }
  .front .divider {
    position: absolute;
    top: 134px;
    left: 0;
    right: 0;
    display: flex;
    align-items: center;
    gap: 12px;
    padding-left: 110px;
  }
  .front .divider .rule { height: 1px; background: var(--rule); }
  .front .divider .rule.short { width: 40px; position: absolute; left: 58px; }
  .front .divider .rule.long { flex: 1; }
  .front .owners { font-size: 16px; }
  .front .contact {
    position: absolute;
    top: 166px;
    left: 150px;
    font-size: 15px;
    line-height: 27px;
    letter-spacing: 0.5px;
  }
  .front .address-band {
    position: absolute;
    bottom: 0;
    left: 0;
    right: 0;
    height: 38px;
    background: linear-gradient(var(--band-light), #c9c9c9);
    color: var(--band-ink);
    font-size: 14.5px;
    letter-spacing: 0.4px;
    display: flex;
    align-items: center;
    justify-content: center;
    font-weight: 400;
  }
  /* Back */
  .back .brand {
    position: absolute;
    top: 92px;
    left: 60px;
    display: flex;
    align-items: center;
    gap: 18px;
  }
  .back .brand-name {
    font-family: "Alike", serif;
    font-size: 40px;
    color: var(--ink-light);
  }
  .back .brand-dot {
    width: 44px;
    height: 44px;
    border-radius: 50%;
    background: var(--ink-light);
  }
  .back .web {
    position: absolute;
    top: 196px;
    left: 60px;
    display: flex;
    align-items: center;
    gap: 16px;
    font-size: 15px;
    letter-spacing: 0.5px;
  }
  .back .web .rule { width: 64px; height: 1px; background: var(--rule); }
</style>
</head>
<body>
  <main class="canvas">
    <section class="card front" aria-label="Card front">
      <div class="title">Blow Dry Bar</div>
      <div class="divider">
        <span class="rule short"></span>
        <span class="owners">Marisol&amp;Tess</span>
        <span class="rule long"></span>
      </div>
      <div class="contact">
        <div>(555) 014-2763</div>
        <div>SIMPLYSWEPTUPWARD.EXAMPLE</div>
        <div>INFO@SIMPLYSWEPTUPWARD.EXAMPLE</div>
      </div>
      <div class="address-band">88 MAPLE RIDGE ROAD SUITE 7 FAIRHAVEN, TEXAS 70412</div>
    </section>
    <section class="card back" aria-label="Card back">
      <div class="brand">
        <span class="brand-name">Simply Swept Upward</span>
        <span class="brand-dot"></span>
      </div>
      <div class="web">
        <span>SIMPLYSWEPTUPWARD.EXAMPLE</span>
        <span class="rule"></span>
      </div>
    </section>
  </main>
</body>
</html>
```